TL - business card

Tallow Partners is an insurance brokerage firm, inovative, proactive, vigorous, which aims to become the leader of the insurance brokers in Anfrica. We should like to get some designs which should be avoided also in Gray / Metallic for the Administration and Orange / Blue for the Managers (ike in the picture sent). The Blue / Green logo is not the correct one, but the source of the file. Please adjust the color accordingly for the business cards. 1 / Orange / Blue 2 / Gray / Metallic We want something classic but which is transmitted strenght, inovation, modernity and most of all, rapidity. We want something start-up like, very punchy and catching eye remaining profesional at the same time. Name: Dorian Whitlock Function: Managing Director Address: N ° 17/18 Rua Veloso - R / C 2B Direita - Bairro Mutamba - Luanda Tel: (+244) 947 582 316 Email: dorian.whitlock@tallow-p.example Website: www.tallow-p. example We want classic in the front and creative, colorfull at the back. The cards will be printed in relief, with very high quality of paper.
Insurance Broker
Colors
Designer to choose colors to be used in the design.

```html
<!DOCTYPE html>
<html lang="en">
<head>
<meta charset="utf-8">
<title>TL - business card</title>
<link href="https://fonts.googleapis.com/css2?family=Lato:wght@400&family=Roboto:wght@700&display=swap" rel="stylesheet">
<style>
  :root {
    --blue: #0b75c1;
    --blue-back: #0b7bc4;
    --red: #df2b27;
    --orange: #f59a57;
    --text-grey: #555759;
    --page: #d6d6d6;
    --card-white: #ffffff;
  }
  * { margin: 0; padding: 0; box-sizing: border-box; }
  html, body {
    width: 1125px; height: 1200px; overflow: hidden;
    background: var(--page);
  }
  .canvas { position: relative; width: 1125px; height: 1200px; }
  .card {
    position: absolute; left: 112px; width: 900px; height: 511px;
    border-radius: 25px; overflow: hidden;
  }
  .card-front { top: 59px; background: var(--card-white); }
  .card-back { top: 630px; background: var(--blue-back); }

  .brand {
    position: absolute; left: 98px; top: 150px; width: 310px;
    display: flex; flex-direction: column; align-items: center; gap: 26px;
  }
  .brand-dot {
    width: 100px; height: 100px; border-radius: 50%;
    background: var(--orange);
  }
  .brand-name {
    font-family: "Roboto", sans-serif; font-weight: 700;
    font-size: 32px; color: var(--blue); white-space: nowrap;
    letter-spacing: 0.3px;
  }

  .divider {
    position: absolute; left: 448px; top: 140px; width: 2px; height: 230px;
    background: linear-gradient(var(--orange), var(--red));
  }

  .details { position: absolute; left: 494px; top: 124px; }
  .person-name {
    font-family: "Roboto", sans-serif; font-weight: 700;
    font-size: 33px; color: var(--blue); letter-spacing: 0.6px; line-height: 44px;
  }
  .person-role, .address, .contact-line {
    font-family: "Lato", sans-serif; font-weight: 400; color: var(--text-grey);
  }
  .person-role { font-size: 21px; margin-top: 4px; }
  .address { font-size: 20px; line-height: 25px; margin-top: 16px; }
  .contacts { list-style: none; margin-top: 20px; }
  .contact-line {
    display: flex; align-items: center; gap: 14px;
    font-size: 20px; height: 35px;
  }
  .contact-line svg { width: 17px; height: 17px; flex: none; fill: var(--blue); }

  .front-band { position: absolute; left: 0; bottom: 0; width: 900px; height: 80px; }

  .back-pattern { position: absolute; inset: 0; background: var(--blue-back); }
  .back-brand {
    position: absolute; left: 640px; top: 345px;
    display: flex; align-items: center; gap: 10px;
  }
  .back-brand .brand-dot { width: 26px; height: 26px; }
  .back-brand-name {
    font-family: "Roboto", sans-serif; font-weight: 700;
    font-size: 18px; color: var(--card-white); white-space: nowrap;
  }
</style>
</head>
<body>
<div class="canvas">
  <section class="card card-front">
    <div class="brand">
      <div class="brand-dot"></div>
      <div class="brand-name">Tallow Partners</div>
    </div>
    <div class="divider"></div>
    <div class="details">
      <h1 class="person-name">Dorian Whitlock</h1>
      <p class="person-role">Managing Director</p>
      <p class="address">&nbsp;N ° 17/18 Rua Veloso - R / C 2B<br>Direita - Bairro Mutamba - Luanda</p>
      <ul class="contacts">
        <li class="contact-line">
          <svg viewBox="0 0 24 24" aria-hidden="true"><path d="M6.6 10.8c1.4 2.8 3.8 5.1 6.6 6.6l2.2-2.2c.3-.3.7-.4 1-.2 1.1.4 2.3.6 3.6.6.6 0 1 .4 1 1V20c0 .6-.4 1-1 1C10.6 21 3 13.4 3 4c0-.6.4-1 1-1h3.5c.6 0 1 .4 1 1 0 1.3.2 2.5.6 3.6.1.3 0 .7-.2 1z"/></svg>
          (+244) 947 582 316
        </li>
        <li class="contact-line">
          <svg viewBox="0 0 24 24" aria-hidden="true"><path d="M2 5h20v14H2zm2 2v10h16V7l-8 6z"/></svg>
          dorian.whitlock@tallow-p.example
        </li>
        <li class="contact-line">
          <svg viewBox="0 0 24 24" aria-hidden="true"><path d="M12 2a10 10 0 1 0 0 20 10 10 0 0 0 0-20zm-1 17.9A8 8 0 0 1 4.2 10L9 14.8V16c0 1 1 2 2 2zm6.9-2.5c-.3-.8-1-1.4-1.9-1.4h-1v-3c0-.6-.4-1-1-1H8v-2h2c.6 0 1-.4 1-1V7h2c1.1 0 2-.9 2-2v-.4a8 8 0 0 1 2.9 12.8z"/></svg>
          www.tallow-p. example
        </li>
      </ul>
    </div>
    <svg class="front-band" viewBox="0 0 900 80" preserveAspectRatio="none" aria-hidden="true">
      <defs>
        <linearGradient id="bandFill" x1="0" x2="1" y1="0" y2="0">
          <stop offset="0" stop-color="#df2b27"/>
          <stop offset="0.5" stop-color="#e6502c"/>
          <stop offset="1" stop-color="#f59a57"/>
        </linearGradient>
      </defs>
      <path d="M0 17 Q450 70 900 17 L900 80 L0 80 Z" fill="url(#bandFill)"/>
      <path d="M5 12 Q450 64 895 12" fill="none" stroke="#0b75c1" stroke-width="5"/>
    </svg>
  </section>

  <section class="card card-back">
    <div class="back-pattern" role="img" aria-label="Faint repeating brand-symbol pattern on blue"></div>
    <div class="back-brand">
      <div class="brand-dot"></div>
      <div class="back-brand-name">Tallow Partners</div>
    </div>
  </section>
</div>
</body>
</html>
```